Stage Design Company Business Card

We are looking to step up up our business card design for our team.

We are a Full service Design and Consultation company for Stage and TV with an emphasis in Theatrical Lighting.

We like our materials to be clean and modern with solid colors free of patterns and gradients. Our brand consists of 4 primary colors Purple, Black, Grey, and White. Provided is our Word Mark as well as our Symbol Logo.

We would like our cards to leave an impression beyond the information, show our attention to design and detail, and make our marks an easily recognized feature (together or apart) for our clients.

We need a warm approachable comfortable feel for some clients, and a professional flair for the board member type clients.

Attached are our brand elements, and our existing cards to give a sense of our style and a glipse at the information we provide on our cards.

Target Market(s)

broad client base from church leaders to high school teachers and architects.

Industry/Entity Type

Business

Contact Information for Business Card

We format our phone number with periods not parenthesis or dashes. Information will be edited for each of our team members, and team member specific cards are not part of this scope, but rather a template so to speak.

Font styles to use
Sans Serif

Colors
6b449b
ffffff
000000
333333
aaaaaa

Requirements
Must have
• Wordmark and logo mark present (does not need to exist on the same side of card)
• Brand Colors,
• Name, Phone, Email, Address.
• Unique choices that make someone stop and take a second look
Nice to have
• It would be nice to somehow convey what we DO, as our brand name does not lend itself to this, outside of an obvious tagline though.....
• social media if not crowded. all of our handles match (instagram, twitter, facebook)
Should not have
• "clipart"

```html
<!DOCTYPE html>
<html lang="en">
<head>
<meta charset="utf-8">
<title>Tessaly Stageworks Business Card</title>
<link rel="stylesheet" href="https://fonts.googleapis.com/css2?family=Jura:wght@400;500&display=swap">
<style>
  :root {
    --stage: #151515;
    --card-white: #ffffff;
    --brand-purple: #3b2669;
    --ink: #000000;
    --ink-grey: #333333;
    --soft-grey: #aaaaaa;
    --on-purple: #ffffff;
  }
  * { box-sizing: border-box; margin: 0; padding: 0; }
  html, body {
    width: 1200px;
    height: 1076px;
    overflow: hidden;
    background: var(--stage);
    font-family: "Jura", sans-serif;
  }
  .sheet {
    position: relative;
    width: 1200px;
    height: 1076px;
  }
  .card {
    position: absolute;
    left: 220px;
    width: 760px;
    height: 438px;
  }
  .card-front {
    top: 80px;
    background: var(--card-white);
    display: flex;
    align-items: center;
    justify-content: center;
  }
  .card-back {
    top: 558px;
    background: var(--brand-purple);
    color: var(--on-purple);
  }
  .brand {
    display: flex;
    align-items: center;
    gap: 18px;
    white-space: nowrap;
  }
  .brand-dot {
    flex: none;
    width: 32px;
    height: 32px;
    border-radius: 50%;
    background: var(--brand-purple);
  }
  .brand-name {
    font-size: 32px;
    font-weight: 500;
    letter-spacing: 0.26em;
    color: var(--ink);
    text-transform: uppercase;
  }
  .card-back .brand {
    position: absolute;
    left: 46px;
    top: 204px;
    gap: 12px;
  }
  .card-back .brand-dot {
    width: 22px;
    height: 22px;
    background: var(--on-purple);
  }
  .card-back .brand-name {
    font-size: 19px;
    color: var(--on-purple);
    letter-spacing: 0.2em;
  }
  .contact {
    position: absolute;
    left: 420px;
    top: 70px;
    width: 310px;
    text-align: center;
    text-transform: uppercase;
  }
  .contact-name {
    font-size: 30px;
    font-weight: 400;
    letter-spacing: 0.05em;
    white-space: nowrap;
  }
  .contact-phone {
    margin-top: 48px;
    font-size: 32px;
    letter-spacing: 0.01em;
  }
  .contact-email {
    margin-top: 22px;
    font-size: 23px;
    text-transform: none;
    letter-spacing: 0.02em;
    white-space: nowrap;
  }
  .contact-address {
    margin-top: 36px;
    font-size: 26px;
    font-style: normal;
    line-height: 1.4;
    letter-spacing: 0.06em;
  }
</style>
</head>
<body>
  <main class="sheet">
    <section class="card card-front" aria-label="Card front">
      <div class="brand">
        <span class="brand-dot"></span>
        <span class="brand-name">Tessaly Stageworks</span>
      </div>
    </section>

    <section class="card card-back" aria-label="Card back">
      <div class="brand">
        <span class="brand-dot"></span>
        <span class="brand-name">Tessaly Stageworks</span>
      </div>
      <div class="contact">
        <h1 class="contact-name">Mara L Tessaly</h1>
        <p class="contact-phone">480.555.0147</p>
        <p class="contact-email">mara@tessaly-s.com</p>
        <address class="contact-address">18 N Cedar St<br>Tempe, AZ 85281</address>
      </div>
    </section>
  </main>
</body>
</html>
```